Business card for medical clinic

I need an upmarket, modern medical/health business card for my clinic

Contact Information for Business Card

name, address, email, qr code

```html
<!DOCTYPE html>
<html lang="en">
<head>
<meta charset="utf-8">
<title>Meridian Care Clinic – Business Card</title>
<link rel="stylesheet" href="https://fonts.googleapis.com/css2?family=Cinzel:wght@500&family=Tinos&display=swap">
<style>
  :root {
    --backdrop: #2a2b2d;
    --card-navy: #1c2232;
    --card-navy-deep: #141925;
    --blue-bright: #14a4e6;
    --blue-deep: #17426b;
    --text-light: #e6e9ef;
    --text-muted: #c9ced8;
    --accent: #1ea8ec;
  }
  * { margin: 0; padding: 0; box-sizing: border-box; }
  html, body {
    width: 1200px; height: 852px; overflow: hidden;
    background: var(--backdrop);
  }
  .canvas {
    position: relative; width: 1200px; height: 852px;
    display: flex; align-items: center; justify-content: center; gap: 60px;
  }
  .card {
    position: relative; width: 500px; height: 286px;
    border-radius: 22px; overflow: hidden;
    box-shadow: 0 14px 30px rgba(0,0,0,.45);
  }
  /* Back side */
  .card-back .pattern-area {
    position: absolute; inset: 0;
    background: linear-gradient(135deg, #1f2537 0%, #151a27 100%);
  }
  .card-back .brand {
    position: absolute; left: 50%; top: 50%;
    transform: translate(-50%, -50%);
    display: flex; align-items: center; gap: 10px;
    color: var(--accent);
  }
  .brand-mark {
    width: 34px; height: 34px; border-radius: 50%;
    border: 2px solid currentColor; flex: none;
  }
  .brand-name {
    font-family: "Cinzel", serif; font-weight: 500;
    font-size: 21px; letter-spacing: .5px; white-space: nowrap;
  }

  /* Front side */
  .card-front { background: var(--card-navy); }
  .card-front .band { position: absolute; inset: 0; }
  .card-front .brand {
    position: absolute; left: 24px; top: 118px;
    display: flex; align-items: center; gap: 10px;
    color: #ffffff;
  }
  .card-front .brand-mark { width: 40px; height: 40px; }
  .card-front .brand-name { font-size: 18px; line-height: 22px; }
  .contact {
    position: absolute; left: 306px; top: 64px;
    font-family: "Tinos", serif; color: var(--text-muted);
  }
  .contact .person-name {
    font-family: "Cinzel", serif; font-weight: 500;
    font-size: 19px; color: var(--accent); letter-spacing: .5px;
  }
  .contact .person-role { font-size: 12.5px; margin: 0 0 16px 12px; color: var(--text-light); }
  .contact-list { list-style: none; font-size: 12px; line-height: 17px; }
  .contact-list li { display: flex; align-items: center; gap: 8px; }
  .contact-list svg { width: 10px; height: 10px; flex: none; fill: var(--text-muted); }
  .contact-list .address { margin-top: 10px; font-size: 12.5px; }
</style>
</head>
<body>
<main class="canvas">

  <section class="card card-back" aria-label="Card back">
    <div class="pattern-area" role="img" aria-label="Dark navy background with embossed repeating circle pattern"></div>
    <div class="brand">
      <span class="brand-mark"></span>
      <span class="brand-name">MERIDIAN CARE CLINIC</span>
    </div>
  </section>

  <section class="card card-front" aria-label="Card front">
    <svg class="band" viewBox="0 0 500 286" width="500" height="286" aria-hidden="true">
      <defs>
        <linearGradient id="bandFill" x1="0" y1="0" x2="1" y2="1">
          <stop offset="0" stop-color="#17426b"/>
          <stop offset="1" stop-color="#14a4e6"/>
        </linearGradient>
      </defs>
      <path d="M0,0 H210 Q292,110 284,286 H0 Z" fill="#1aa0dd"/>
      <path d="M0,0 H198 Q276,110 270,286 H0 Z" fill="url(#bandFill)"/>
    </svg>

    <div class="brand">
      <span class="brand-mark"></span>
      <span class="brand-name">MERIDIAN CARE<br>CLINIC</span>
    </div>

    <div class="contact">
      <h1 class="person-name">DANIEL HALE</h1>
      <p class="person-role">Managing Director</p>
      <ul class="contact-list">
        <li>
          <svg viewBox="0 0 10 10"><path d="M2 0.5 L3.6 2.4 L2.8 3.5 Q4 5.8 6.5 7.2 L7.6 6.4 L9.5 8 L8.2 9.5 Q3.5 9 0.5 1.8 Z"/></svg>
          0555-123-45678
        </li>
        <li>
          <svg viewBox="0 0 10 10"><path d="M0.5 2 H9.5 V8.5 H0.5 Z M1 2.4 L5 5.6 L9 2.4"/></svg>
          info@meridiancare.com
        </li>
        <li>
          <svg viewBox="0 0 10 10"><circle cx="5" cy="5" r="4.5"/></svg>
          www.meridiancare.com
        </li>
        <li class="address">48, Oak Lane, Town, US 123456</li>
      </ul>
    </div>
  </section>

</main>
</body>
</html>
```